Quorimo Business Card Design Project

We need a business card design for quorimo.example a company based in Berlin, Germany.

?Quorimo is marketplace that enables people all over the world to monetize and exchange their individual knowledge and language skills through interactive video sessions. User are matched by their interests.

On Quorimo everybody can be student or teacher (seller or buyer).

We would love to see designs that use or main color blue and green. The design should communicate what Quorimo enables - see my notice above.

Looking so forward to your designs
Cheers from Berlin,
Lorenz

Target Market(s)

globally

Industry/Entity Type

Teacher

Requirements
Must have
• Lorenz Hubeck
CEO
Quorimo.example

Quorimo e-Services GmbH
Lindenweg 87
10247 Berlin

Fon: +49 30 418 906 25 17
Mobile: 49 172 54 91 37 6
E-Mail: l.hubeck@quorimo.example
Web: www.quorimo.example

```html
<!DOCTYPE html>
<html lang="de">
<head>
<meta charset="utf-8">
<title>Quorimo – Visitenkarte</title>
<link rel="stylesheet" href="https://fonts.googleapis.com/css2?family=Open+Sans:wght@400;700&display=swap">
<style>
  :root {
    --backdrop: #d9d9d9;
    --card: #ffffff;
    --brand-blue: #1ea3dc;
    --brand-grey: #646464;
    --ink: #2b2b2b;
    --rule: #8a8a8a;
  }
  * { margin: 0; padding: 0; box-sizing: border-box; }
  html, body { width: 954px; height: 1200px; overflow: hidden; }
  body {
    position: relative;
    background: var(--backdrop);
    font-family: "Open Sans", Arial, sans-serif;
    color: var(--ink);
  }
  .card {
    position: absolute;
    left: 76px;
    width: 798px;
    height: 454px;
    background: var(--card);
    border-radius: 24px;
    box-shadow: 0 3px 10px rgba(0,0,0,0.18);
    overflow: hidden;
  }
  .card--front { top: 88px; }
  .card--back { top: 645px; }

  .wordmark {
    position: absolute;
    display: flex;
    align-items: center;
    gap: 18px;
  }
  .wordmark__square {
    width: 76px;
    height: 76px;
    background: var(--brand-blue);
  }
  .wordmark__name {
    font-size: 84px;
    font-weight: 400;
    line-height: 1;
    color: var(--brand-grey);
    letter-spacing: 1px;
  }
  .card--front .wordmark { left: 38px; top: 50px; }
  .card--back .wordmark { left: 164px; top: 170px; }

  .person {
    position: absolute;
    left: 44px;
    top: 246px;
    font-size: 17px;
  }
  .person__name {
    font-size: 24px;
    font-weight: 700;
    color: var(--brand-blue);
  }
  .person__role { margin-left: 6px; }

  .contact {
    position: absolute;
    left: 40px;
    top: 320px;
    list-style: none;
    font-size: 17px;
    line-height: 26.5px;
  }
  .contact__label { font-weight: 700; }

  .divider {
    position: absolute;
    left: 349px;
    top: 324px;
    width: 1.5px;
    height: 103px;
    background: var(--rule);
  }
  .address {
    position: absolute;
    left: 366px;
    top: 347px;
    font-style: normal;
    font-size: 17px;
    line-height: 26.5px;
  }
</style>
</head>
<body>
  <section class="card card--front" aria-label="Vorderseite">
    <div class="wordmark">
      <span class="wordmark__square"></span>
      <span class="wordmark__name">quorimo</span>
    </div>

    <p class="person">
      <span class="person__name">Lorenz Hubeck</span>
      <span class="person__role">| CEO</span>
    </p>

    <ul class="contact">
      <li><span class="contact__label">Fon :</span> +49 30 418 906 25 17</li>
      <li><span class="contact__label">Mobile :</span> 49 172 54 91 37 6</li>
      <li><span class="contact__label">E-Mail :</span> l.hubeck@quorimo.example</li>
      <li><span class="contact__label">Web :</span> www.quorimo.example</li>
    </ul>

    <span class="divider"></span>

    <address class="address">
      Quorimo e-Services GmbH<br>
      Lindenweg 87<br>
      10247 Berlin
    </address>
  </section>

  <section class="card card--back" aria-label="Rückseite">
    <div class="wordmark">
      <span class="wordmark__square"></span>
      <span class="wordmark__name">quorimo</span>
    </div>
  </section>
</body>
</html>
```